Web Design Project - Shipping Industry

Goals and Objectives
The objective of the new website is to create a more modern look and feel. The site will also allow for a more effective means of communicating with members while providing the public with information and developments in the local, regional and international shipping industry.
Scope
The website will highlight the history of the organisation inclusive of text and photographs. It will take visitors through the years from beginning to present. Information on the history of the shipping industry will also be included.
It will feature current articles on the organisation, its members and stakeholders in the shipping industry. Member information as well as pertinent details regarding the organisation’s subsidiaries will be documented for the website.
Information as it relates to shipping statistics, case studies, laws and regulations, international treaties and trade documents, shipping terms, careers in shipping, job opportunities, training opportunities, information for shippers including port listing and trade lanes will be main features of the content for the website.
The Association’s community involvement, industry calendar events and related links relevant industry members will also be featured.
Target Market
• The General Public;
• Members of the organization;
• Shipping Industry Stakeholders (local, regional and international);
• Tertiary students conducting research.
• Potential employees
• Potential Business Partners
Best Practice Bench Marketing
The following websites are being looked at:
• Korvel Quayworks - http://www.korvelquayworks.example/ (preferred look)
• Tessaly Maritime Association - http://www.tma-freight.example/ (like image transition on main page)
• Drovna - http://www.drovna.example (professional look)
• PLW - http://www.pelworth.example (preferred color: blue in logo)
• Quillo - http://www.quillo.example/electronics/tv-video-audio/ (preferred look for links page: image + short text below + visit site link)
Expected Result
• 3 - 5 pages which must include: [1] main page [2] standard page [3] links page

```html
<!DOCTYPE html>
<html lang="en">
<head>
<meta charset="utf-8">
<title>Meridane – About Us</title>
<link rel="stylesheet" href="https://fonts.googleapis.com/css2?family=Questrial&family=Noto+Sans:wght@400;700&display=swap">
<style>
:root{
  --navy:#1c1f66;
  --blue:#0a4ab5;
  --link:#1a7fb0;
  --orange:#e2491b;
  --text:#333;
  --muted:#666;
  --rule:#d4d4d4;
  --footer-bg:#ececec;
  --heading-font:"Questrial",sans-serif;
  --body-font:"Noto Sans",sans-serif;
}
*{margin:0;padding:0;box-sizing:border-box}
html,body{width:929px;height:1200px;overflow:hidden;background:#fff}
body{position:relative;font-family:var(--body-font);color:var(--text)}
a{text-decoration:none;color:inherit}
.abs{position:absolute}
.social{display:flex;gap:7px}
.social span{width:20px;height:20px;border-radius:50%;background:var(--blue);display:block;box-shadow:inset 0 0 0 2px #b9c9e6}
.brand{left:92px;top:50px;font-family:var(--heading-font);font-size:25px;letter-spacing:4px;color:var(--navy)}
.tagline{left:93px;top:79px;font-family:var(--heading-font);font-size:12.5px;color:var(--orange)}
.search{left:676px;top:46px;width:159px;height:20px;border:1px solid #ccc;border-radius:10px;box-shadow:inset 0 1px 3px #ddd}
.search-btn{left:809px;top:45px;width:26px;height:21px;border-radius:11px;background:var(--blue)}
.main-nav{left:412px;top:86px;display:flex;gap:21px;font-family:var(--heading-font);font-size:10px;color:var(--link)}
.banner{left:92px;top:128px;width:743px;height:49px;background:var(--blue);color:#fff;font-size:8.6px;padding:18px 24px}
.banner b{font-family:var(--heading-font);font-size:9.5px}
.crumb{left:266px;top:186px;font-size:8.5px;color:#888}
.crumb em{font-style:normal;color:#444}
.side-nav{right:715px;top:220px;text-align:right;font-family:var(--heading-font);font-size:10px;color:var(--link);line-height:23.2px}
.page-title{left:266px;top:212px;font-family:var(--heading-font);font-size:21px;color:var(--navy)}
.section-title{left:266px;width:569px;font-family:var(--heading-font);font-size:14.5px;color:var(--navy);border-bottom:1px solid var(--rule);padding-bottom:5px}
.copy{left:266px;width:560px;font-size:8.4px;line-height:10.3px;color:#444}
.work-title{left:266px;top:502px;font-family:var(--heading-font);font-size:14.5px;color:var(--orange)}
.work-photo{left:264px;top:529px;width:282px;height:141px;border:2px solid #a9b3c4;background:linear-gradient(135deg,#dfe8f7,#8fa9dc 55%,#4f6fb7)}
.ticks{left:582px;top:533px;list-style:none;font-size:8.8px;line-height:18.6px;color:#444}
.ticks li{display:flex;align-items:center;gap:7px}
.rule{left:92px;width:743px;height:1px;background:var(--rule)}
.partners{left:92px;top:815px;width:743px;display:flex;justify-content:space-around;align-items:center;height:60px}
.partner{display:flex;align-items:center;gap:6px;font-family:var(--heading-font);font-size:13px;color:var(--navy)}
.partner i{width:14px;height:14px;border-radius:50%;background:var(--blue);display:block}
.footer-cols{left:92px;top:929px;display:flex}
.footer-col h4{font-family:var(--heading-font);font-weight:400;font-size:12px;color:var(--link);margin-bottom:8px}
.footer-col ul{list-style:none;font-size:8.6px;line-height:14px;color:#555}
.footer-band{left:0;top:1066px;width:929px;height:134px;background:var(--footer-bg)}
.footer-nav{left:93px;top:1085px;display:flex;gap:19px;font-family:var(--heading-font);font-size:9px;color:var(--navy)}
.footer-brand{left:92px;top:1130px;font-family:var(--heading-font);font-size:21px;letter-spacing:4px;color:#9c9c9c}
.copyright{left:93px;top:1163px;font-size:8.5px;color:#777}
.connect-title{left:633px;top:1081px;font-family:var(--heading-font);font-size:12px;color:#333}
.connect-box{left:630px;top:1101px;width:206px;height:67px;background:#fff;border:1px solid #d5d5d5;padding:10px 12px 0 13px;font-size:8px;line-height:9.6px;color:#444}
.connect-box p.meta{margin-top:8px;color:var(--orange);font-size:8px}
.connect-box p.meta em{margin-left:8px}
</style>
</head>
<body>
  <div class="abs social" style="left:739px;top:6px"><span></span><span></span><span></span><span></span></div>

  <div class="abs brand">MERIDANE</div>
  <div class="abs tagline">The Shipping Organisation</div>

  <div class="abs search"></div>
  <div class="abs search-btn">
    <svg width="26" height="21" viewBox="0 0 26 21"><circle cx="12" cy="9" r="3.6" fill="none" stroke="#fff" stroke-width="1.8"/><line x1="14.6" y1="11.6" x2="18" y2="15" stroke="#fff" stroke-width="2.2" stroke-linecap="round"/></svg>
  </div>

  <nav class="abs main-nav"><a>ABOUT US</a><a>HOW WE WORK</a><a>OUR SERVICES</a><a>WHY US</a><a>NEWS AND UPDATES</a></nav>

  <div class="abs banner"><b>CURABITUR EU PORTTITOR NEQUE.</b> Lorem ipsum dolor sit amet, consectetur adipiscing elit. Pellentesque gravida luctus tortor.</div>

  <div class="abs crumb">Home &gt; <em>About Us</em></div>

  <nav class="abs side-nav">
    <div>HOME</div><div>ABOUT US</div><div>HOW WE WORK</div><div>OUR SERVICES</div><div>WHY US</div><div>NEWS AND UPDATES</div><div>ABOUT ORGANISATIONS</div><div>ABOUT MEMBERS</div><div>FAQS</div><div>CONTACT US</div>
  </nav>

  <h1 class="abs page-title">ABOUT US</h1>

  <h2 class="abs section-title" style="top:277px">About Us</h2>
  <p class="abs copy" style="top:314px">Fusce quis lacus diam, sit amet sollicitudin ante. Quisque ultricies dolor sit amet enim malesuada consectetur. Maecenas vulputate tellus nec orci posuere interdum. Suspendisse potenti. Fusce qis enim massa. Ut tempor turpis non dolor feugiat vel tempus ligula malesuada nibh erat, euismod ac interdum non, lacinia eu massa. Maecenas vulputate tellus nec orci posure interdum. Suspendisse potenti. Fusce qis enim massa. Ut tempor turpis non dolor feugiat.</p>

  <h2 class="abs section-title" style="top:391px">Lorem Ipsum Title</h2>
  <p class="abs copy" style="top:429px">Fusce quis lacus diam, sit amet sollicitudin ante. Quisque ultricies dolor sit amet enim malesuada consectetur. Maecenas vulputate tellus nec orci posuere interdum. Suspendisse potenti. Fusce qis enim massa. Ut tempor turpis non dolor feugiat vel tempus ligula malesuada nibh erat, euismod ac interdum non, lacinia eu massa. Maecenas vulputate tellus nec orci posure interdum. Suspendisse potenti. Fusce qis enim massa. Ut tempor turpis non dolor feugiat.</p>

  <h2 class="abs work-title">How We Work</h2>
  <div class="abs work-photo" role="img" aria-label="Blue-toned photo of a pen tracing a line chart on a financial report"></div>

  <ul class="abs ticks">
    <li><svg width="13" height="11" viewBox="0 0 13 11"><path d="M1 6l3.5 3.5L12 1" fill="none" stroke="#e2491b" stroke-width="2.4"/></svg>Fusce quis lacus diam, sit amet sollicitudin</li>
    <li><svg width="13" height="11" viewBox="0 0 13 11"><path d="M1 6l3.5 3.5L12 1" fill="none" stroke="#e2491b" stroke-width="2.4"/></svg>Quisque ultricies dolor sit amet enim malesuada</li>
    <li><svg width="13" height="11" viewBox="0 0 13 11"><path d="M1 6l3.5 3.5L12 1" fill="none" stroke="#e2491b" stroke-width="2.4"/></svg>Maecenas vulputate tellus nec orci posuere</li>
    <li><svg width="13" height="11" viewBox="0 0 13 11"><path d="M1 6l3.5 3.5L12 1" fill="none" stroke="#e2491b" stroke-width="2.4"/></svg>Suspendisse potenti eusce qis enim massa</li>
    <li><svg width="13" height="11" viewBox="0 0 13 11"><path d="M1 6l3.5 3.5L12 1" fill="none" stroke="#e2491b" stroke-width="2.4"/></svg>Ut tempor turpis non dolor feugiat</li>
    <li><svg width="13" height="11" viewBox="0 0 13 11"><path d="M1 6l3.5 3.5L12 1" fill="none" stroke="#e2491b" stroke-width="2.4"/></svg>Maecenas vulputate tellus nec orci posure</li>
    <li><svg width="13" height="11" viewBox="0 0 13 11"><path d="M1 6l3.5 3.5L12 1" fill="none" stroke="#e2491b" stroke-width="2.4"/></svg>Suspendisse potenti qis enim massa</li>
  </ul>

  <div class="abs rule" style="top:791px"></div>
  <div class="abs partners">
    <div class="partner"><i></i>Calvreth Lines</div>
    <div class="partner"><i></i>Pellan Marine</div>
    <div class="partner"><i></i>Orsk Freight</div>
    <div class="partner"><i></i>Hallow Bay Shipping</div>
    <div class="partner"><i></i>Verrin Cargo</div>
  </div>
  <div class="abs rule" style="top:894px"></div>

  <div class="abs footer-cols">
    <div class="footer-col" style="width:127px"><h4>Getting Started</h4><ul><li>Getting started</li><li>About Meridane</li><li>About Organisations</li><li>About Members</li><li>Current Articles</li></ul></div>
    <div class="footer-col" style="width:132px"><h4>Statistics</h4><ul><li>Shipping Statistics</li><li>Case Studies</li><li>Laws And Regulations</li><li>About Organisations</li><li>About Members</li></ul></div>
    <div class="footer-col" style="width:136px"><h4>Legal</h4><ul><li>International Treaties</li><li>Trade Documents</li><li>Shipping Terms</li><li>Privacy Policy</li><li>Disclaimer</li></ul></div>
    <div class="footer-col" style="width:126px"><h4>Careers</h4><ul><li>Careers in Shipping</li><li>Job Opportunities</li><li>Training Opportunities</li></ul></div>
    <div class="footer-col" style="width:133px"><h4>For Shipping</h4><ul><li>Port Listing</li><li>Trade Lanes</li><li>More About Shipping</li></ul></div>
    <div class="footer-col"><h4>Community</h4><ul><li>About Community</li><li>Calendar Events</li><li>Industry Memebers</li><li>Related Links</li><li>More Related Links</li></ul></div>
  </div>

  <div class="abs footer-band"></div>
  <nav class="abs footer-nav"><a>ABOUT US</a><a>HOW WE WORK</a><a>OUR SERVICES</a><a>WHY MERIDANE</a><a>NEWS AND UPDATES</a></nav>
  <div class="abs footer-brand">MERIDANE</div>
  <div class="abs copyright">© Copyright 2012. All Rights Reserved.</div>

  <div class="abs connect-title">Connect With Us</div>
  <div class="abs connect-box">
    <p>Praesent tempus sagittis elementum. Prsent id quam erat, sit amet condimentum neque. Phasellus quis est nisi. Ut luctus adipiscing.</p>
    <p class="meta">Lorem Ipsum <em>2 hours ago</em></p>
  </div>
  <div class="abs social" style="left:632px;top:1173px;gap:7px"><span></span><span></span><span></span><span></span></div>
</body>
</html>
```